Creative Brief
Brand Packaging Identity V
KALMO
Pose your way
Innovation and Creativity are the cornerstones in the foundation of KALMO. The most accurate quartz watches in the industry, ruggedized for use by those that live, work and play in truly adverse conditions. Water and Shock resistant, the line of technology used is advanced and inventive at the same time, for those whose usage demanded certain durability.
Jewelry
the back dial should consist of some art work as shown as an example in the briefing.

```html
<!DOCTYPE html>
<html lang="en">
<head>
<meta charset="utf-8">
<title>KALMO — Packaging Identity</title>
<link rel="stylesheet" href="https://fonts.googleapis.com/css2?family=Cinzel:wght@500&family=Montserrat:wght@400;600&display=swap">
<style>
:root{
  --bg:#2b2b2b;
  --panel:#0c0c0c;
  --panel-edge:#1d1d1d;
  --gold:#b89a5c;
  --white:#f3f3f3;
  --muted:#8a8a8a;
  --steel:#cfd2d4;
}
*{box-sizing:border-box;margin:0;padding:0}
html,body{width:1200px;height:751px;overflow:hidden;background:var(--bg)}
.canvas{position:relative;width:1200px;height:751px;background:var(--bg);font-family:"Montserrat",sans-serif}
.p{position:absolute;background:var(--panel);border:1px solid var(--panel-edge)}
.brand{font-family:"Cinzel",serif;font-weight:500;color:var(--gold);letter-spacing:.12em;text-align:center;line-height:1}
.mark{display:block;margin:0 auto 6px;width:10px;height:10px;background:var(--gold)}
.lockup{position:absolute;left:0;right:0;text-align:center}
.url{position:absolute;left:0;right:0;text-align:center;font-size:5px;color:var(--muted);letter-spacing:.05em}
.vert{position:absolute;left:50%;top:50%;transform:translate(-50%,-50%) rotate(-90deg);white-space:nowrap;font-size:7px}
.tag{position:absolute}
.tag svg{position:absolute;inset:0}
.tag .lockup{top:34px}
.guarantee{position:absolute;left:8px;right:8px;top:70px;height:18px;background:var(--white);font-size:10px;font-weight:600;color:#111;display:flex;align-items:center;justify-content:center}
.fields{position:absolute;left:22px;right:18px;top:66px}
.field{display:flex;align-items:center;gap:4px;margin-bottom:4px;font-size:6px;color:var(--white)}
.field span:last-child{flex:1;height:9px;background:var(--white)}
.checks{position:absolute;left:8px;right:8px;bottom:8px;display:flex;gap:4px;justify-content:center}
.checks span{width:16px;height:14px;background:var(--white)}
.sleeve{position:absolute;top:96px;width:50px;height:192px;border:1px solid var(--panel-edge)}
.sleeve.dark{background:var(--panel)}
.sleeve.light{background:var(--white)}
.sleeve.light .brand{color:#222}
.band{position:absolute;left:0;right:0;height:24px;background:var(--panel)}
.watch{position:absolute;top:96px;width:150px;height:168px;border-radius:10px}
.watch.silver{left:834px;background:radial-gradient(circle at 50% 50%,#f4f4f4 0 34%,#9a9a9a 35% 40%,#151515 41%)}
.watch.black{left:990px;background:radial-gradient(circle at 50% 50%,#1a1a1a 0 34%,#a0a0a0 35% 40%,#151515 41%)}
.handle{position:absolute;left:960px;top:366px}
</style>
</head>
<body>
<main class="canvas">

  <!-- Guarantee tags -->
  <div class="tag" style="left:84px;top:120px;width:144px;height:156px">
    <svg viewBox="0 0 144 156" width="144" height="156"><path d="M72 0 C100 30 144 60 144 96 A72 60 0 0 1 0 96 C0 60 44 30 72 0Z" fill="var(--panel)"/></svg>
    <div class="lockup"><span class="mark"></span><div class="brand" style="font-size:14px">KALMO</div></div>
    <div class="guarantee">Guarantee Card</div>
    <div class="url" style="bottom:26px">www.kalmowatch.com</div>
  </div>
  <div class="tag" style="left:228px;top:120px;width:144px;height:156px">
    <svg viewBox="0 0 144 156" width="144" height="156"><path d="M72 0 C100 30 144 60 144 96 A72 60 0 0 1 0 96 C0 60 44 30 72 0Z" fill="var(--panel)"/></svg>
    <div class="lockup"><span class="mark"></span><div class="brand" style="font-size:14px">KALMO</div></div>
    <div class="fields">
      <div class="field"><span>Date</span><span></span></div>
      <div class="field"><span>Model</span><span></span></div>
      <div class="field"><span>Serial</span><span></span></div>
    </div>
    <div class="url" style="bottom:26px">Keep this card safe</div>
  </div>

  <!-- Main watch box dieline -->
  <div class="p" style="left:432px;top:96px;width:144px;height:72px">
    <div class="lockup" style="top:26px"><span class="mark" style="width:6px;height:6px;margin-bottom:3px"></span><div class="brand" style="font-size:7px">KALMO</div></div>
  </div>
  <div class="p" style="left:384px;top:168px;width:48px;height:192px"><div class="brand vert">KALMO</div></div>
  <div class="p" style="left:432px;top:168px;width:144px;height:192px">
    <div class="lockup" style="top:76px"><span class="mark"></span><div class="brand" style="font-size:18px">KALMO</div></div>
    <div class="url" style="bottom:10px">www.kalmowatch.com</div>
  </div>
  <div class="p" style="left:576px;top:168px;width:48px;height:192px"><div class="brand vert">KALMO</div></div>
  <div class="p" style="left:432px;top:360px;width:144px;height:48px">
    <div class="checks"><span></span><span></span><span></span><span></span><span></span></div>
  </div>

  <!-- Strap sleeves -->
  <div class="sleeve dark" style="left:640px"><div class="brand vert">KALMO</div></div>
  <div class="sleeve light" style="left:702px">
    <div class="band" style="top:0"></div><div class="band" style="bottom:0"></div>
    <div class="brand vert">KALMO</div>
  </div>
  <div class="sleeve light" style="left:764px"><div class="brand vert">KALMO</div></div>

  <!-- Watches -->
  <div class="watch silver" role="img" aria-label="Photo of a silver-dial watch on a black leather strap"></div>
  <div class="watch black" role="img" aria-label="Photo of a black-dial watch on a black leather strap"></div>

  <!-- Small hang tags -->
  <div class="tag" style="left:840px;top:288px;width:90px;height:108px">
    <svg viewBox="0 0 90 108" width="90" height="108"><path d="M45 0 C62 20 90 40 90 66 A45 42 0 0 1 0 66 C0 40 28 20 45 0Z" fill="var(--panel)"/><circle cx="45" cy="22" r="4" fill="var(--bg)"/><rect x="8" y="56" width="74" height="14" fill="var(--white)"/></svg>
    <div class="brand" style="position:absolute;left:0;right:0;top:60px;font-size:7px;color:#111">KALMO</div>
  </div>
  <div class="tag" style="left:940px;top:288px;width:90px;height:108px">
    <svg viewBox="0 0 90 108" width="90" height="108"><path d="M45 0 C62 20 90 40 90 66 A45 42 0 0 1 0 66 C0 40 28 20 45 0Z" fill="var(--panel)"/><circle cx="45" cy="22" r="4" fill="var(--bg)"/></svg>
    <div class="lockup" style="top:50px"><span class="mark" style="width:7px;height:7px;margin-bottom:4px"></span><div class="brand" style="font-size:9px">KALMO</div></div>
  </div>
  <div class="tag" style="left:1040px;top:288px;width:90px;height:108px">
    <svg viewBox="0 0 90 108" width="90" height="108"><path d="M45 0 C62 20 90 40 90 66 A45 42 0 0 1 0 66 C0 40 28 20 45 0Z" fill="var(--panel)"/><circle cx="45" cy="22" r="4" fill="var(--bg)"/></svg>
    <div class="lockup" style="top:50px"><span class="mark" style="width:7px;height:7px;margin-bottom:4px"></span><div class="brand" style="font-size:9px">KALMO</div></div>
  </div>

  <!-- Cross box dieline -->
  <div class="p" style="left:180px;top:348px;width:108px;height:102px"><div class="brand vert" style="transform:translate(-50%,-50%) rotate(180deg)">KALMO</div></div>
  <div class="p" style="left:96px;top:450px;width:84px;height:108px"><div class="brand vert">KALMO</div></div>
  <div class="p" style="left:180px;top:450px;width:108px;height:108px">
    <div class="lockup" style="top:40px"><span class="mark"></span><div class="brand" style="font-size:13px">KALMO</div></div>
  </div>
  <div class="p" style="left:288px;top:450px;width:84px;height:108px"><div class="brand vert" style="transform:translate(-50%,-50%) rotate(90deg)">KALMO</div></div>
  <div class="p" style="left:180px;top:558px;width:108px;height:126px"><div class="url" style="bottom:12px">www.kalmowatch.com</div></div>

  <!-- Small box dieline -->
  <div class="p" style="left:432px;top:444px;width:108px;height:48px"></div>
  <div class="p" style="left:384px;top:492px;width:48px;height:120px"></div>
  <div class="p" style="left:432px;top:492px;width:108px;height:120px">
    <div class="lockup" style="top:42px"><span class="mark"></span><div class="brand" style="font-size:13px">KALMO</div></div>
  </div>
  <div class="p" style="left:540px;top:492px;width:48px;height:120px"><div class="brand vert" style="transform:translate(-50%,-50%) rotate(90deg)">KALMO</div></div>
  <div class="p" style="left:432px;top:612px;width:108px;height:72px"><div class="url" style="bottom:10px">www.kalmowatch.com</div></div>

  <!-- Die-cut shopping bag -->
  <div class="p" style="left:588px;top:396px;width:180px;height:252px">
    <div style="position:absolute;left:66px;top:18px;width:48px;height:16px;border-radius:8px;background:var(--bg)"></div>
    <div class="lockup" style="top:120px"><span class="mark"></span><div class="brand" style="font-size:18px">KALMO</div></div>
    <div class="url" style="bottom:14px">www.kalmowatch.com</div>
  </div>

  <!-- Paper bag with rope handle -->
  <svg class="handle" width="130" height="70" viewBox="0 0 130 70"><path d="M20 70 C20 0 110 0 110 70" fill="none" stroke="var(--white)" stroke-width="3"/></svg>
  <div class="p" style="left:780px;top:420px;width:120px;height:228px"><div class="brand vert" style="font-size:8px">KALMO</div></div>
  <div class="p" style="left:900px;top:420px;width:228px;height:228px">
    <div class="lockup" style="top:96px"><span class="mark"></span><div class="brand" style="font-size:20px">KALMO</div></div>
    <div class="url" style="bottom:14px">www.kalmowatch.com</div>
  </div>

</main>
</body>
</html>
```